VOMRA Pty Ltd Business Card

Looking for a simple yet eye-catching double-sided business card design using my company logo on one side and contact details on the other.

Target Market(s)

Government

Industry/Entity Type

Communication Systems Engineering

Contact Information for Business Card

VOMRA Pty Ltd

Requirements
Nice to have
• Would be great to have a QR code so details can be scanned into contacts

```html
<!DOCTYPE html>
<html lang="en">
<head>
<meta charset="utf-8">
<title>VOMRA Pty Ltd Business Card</title>
<link href="https://fonts.googleapis.com/css2?family=Arimo:wght@400;700&display=swap" rel="stylesheet">
<style>
  :root {
    --stage: #3a3a3a;
    --card-dark: #2e373f;
    --card-light: #f7f7f7;
    --ink: #2b333b;
    --ink-soft: #6a6f74;
    --white: #ffffff;
    --trace-light: #e6e6e6;
    --trace-dark: #c9c9c9;
  }
  * { box-sizing: border-box; margin: 0; padding: 0; }
  html, body { width: 1200px; height: 689px; overflow: hidden; }
  body {
    background: var(--stage);
    font-family: "Arimo", Arial, sans-serif;
    position: relative;
  }
  .card {
    position: absolute;
    top: 196px;
    width: 520px;
    height: 297px;
    border-radius: 18px;
    overflow: hidden;
  }
  .card--front { left: 50px; background: var(--card-dark); }
  .card--back { left: 630px; background: var(--card-light); }

  .brand {
    display: flex;
    align-items: center;
    gap: 14px;
  }
  .brand__dot {
    width: 14px; height: 14px; border-radius: 50%;
  }
  .brand__name {
    font-weight: 700;
    letter-spacing: 2px;
  }
  .card--front .brand {
    position: absolute;
    left: 50%; top: 50%;
    transform: translate(-50%, -50%);
  }
  .card--front .brand__dot { background: var(--white); }
  .card--front .brand__name { color: var(--white); font-size: 64px; }

  .card--back .brand {
    position: absolute;
    top: 30px; right: 36px;
  }
  .card--back .brand__dot { background: var(--ink); width: 10px; height: 10px; }
  .card--back .brand__name { color: var(--ink); font-size: 38px; }

  .circuit-art {
    position: absolute;
    left: 0; bottom: 0;
    width: 250px; height: 210px;
    background: linear-gradient(135deg, var(--trace-light), var(--trace-dark));
    border-top-right-radius: 40px;
  }

  .contact {
    position: absolute;
    right: 36px; top: 94px;
    text-align: right;
    color: var(--ink);
  }
  .contact__name { font-weight: 700; font-size: 21px; }
  .contact__role { font-size: 11px; color: var(--ink-soft); margin-top: 2px; }
  .contact__address { font-size: 12px; line-height: 1.45; margin-top: 16px; color: var(--ink); }
  .contact__list { list-style: none; margin-top: 14px; font-size: 12px; line-height: 1.6; }
  .contact__list li { display: flex; align-items: center; justify-content: flex-end; gap: 7px; }
  .contact__list svg { width: 11px; height: 11px; fill: var(--ink); }
</style>
</head>
<body>
  <section class="card card--front" aria-label="Card front">
    <div class="brand">
      <span class="brand__dot"></span>
      <span class="brand__name">VOMRA</span>
    </div>
  </section>

  <section class="card card--back" aria-label="Card back">
    <div class="circuit-art" role="img" aria-label="Circuit-board trace pattern in black on white"></div>

    <div class="brand">
      <span class="brand__dot"></span>
      <span class="brand__name">VOMRA</span>
    </div>

    <div class="contact">
      <p class="contact__name">Daniel Mercer</p>
      <p class="contact__role">Managing Director</p>
      <p class="contact__address">4120 Harbour Street<br>Fremantle, WA 6160</p>
      <ul class="contact__list">
        <li>555-210-4780
          <svg viewBox="0 0 24 24" aria-hidden="true"><path d="M6.6 10.8a15 15 0 0 0 6.6 6.6l2.2-2.2a1 1 0 0 1 1-.25 11.4 11.4 0 0 0 3.6.57 1 1 0 0 1 1 1V20a1 1 0 0 1-1 1A17 17 0 0 1 3 4a1 1 0 0 1 1-1h3.5a1 1 0 0 1 1 1c0 1.25.2 2.45.57 3.57a1 1 0 0 1-.25 1z"/></svg>
        </li>
        <li>info@vomra.net
          <svg viewBox="0 0 24 24" aria-hidden="true"><path d="M2 5h20v14H2z M4 7v.5l8 5 8-5V7l-8 5z" fill-rule="evenodd"/></svg>
        </li>
        <li>www.vomra.net
          <svg viewBox="0 0 24 24" aria-hidden="true"><circle cx="12" cy="12" r="10"/></svg>
        </li>
      </ul>
    </div>
  </section>
</body>
</html>
```